Clean & Inspiring Web Design Project

Tallowmere Object Works, LLC (also known as T7-Works) is a company which provides 3D printing services and products. The emphasis is on making these products and services available to the mass-market - customers and users who may or may not have prior experience with 3D printing and/or rapid prototyping technologies. We are a start-up company, looking to build a clean and creativity inspiring brand - our site must encourage visitor to engage and make something. Our aim is to help take mere ideas and turn them into tangible items. We want to show a fusion of ideas (e.g. pencil sketches on graph paper) with design tools (e.g. CAD and drafting software) and rapid prototyping (e.g. Kindlo 3D printers, Stereolithography Machines, etc.). We would like the website to appear professional but at the same time easy to navigate and a good balance between text and pictures. The final design should inspire customers to nurture their ideas into real products and communicate our services to our customers. Our site should have the feel of a vibrant social community with the added benefit of tangible physical creations.

Target Market(s)

People with great ideas that need to be designed into a real product

Industry/Entity Type

Printing

Requirements
Must have
• - Website design should include 2 layouts - one for a "landing page" and one for a "content page"
- Website design must incorporate attached company logo (or derivative of this logo)
- Website design should incorporate the menu options shown in the attached PDF UI concept (UI does not necessarily need to look like the provided concept, just include all the clickable elements)
- Website design must portray an innovative and cooperative design environment with a look-and-feel that appeals to both amateur and professional designers.
- Please include pictures, illustrations and photographs (as needed) related to 3D printing, CAD design, conventional drafting, engineering and manufacturing industries.
- Design should support scaling to multiple screen sizes, from tablet computers (e.g. Zelo) to very large screen PCs.
- Design should include Username & Password fields for login or a button to pull up a login popup.
Nice to have
• - Website design could include "Invent", "Make", "Produce" and "Buy" options that slowly cycle through - with appropriate photos / graphics. These "menu options" would also be mouse-over enabled to switch into the appropriate context as the cursor enters that region (e.g. mouse over the "Invent" text would bring up page 2, etc.). (See attached Original UI Thoughts)
Should not have
• Requirements - Should Not Have:
- Website design should not portray a service that is very expensive or complicated - we are a reasonably priced service meant to be friendly with amateur inventors
- Website design should not be overly complicated - please keep it reasonably simple
- Website design should not be overly trendy
- Website design should not use more than 2 font styles, gaudy fonts, etc.
- Website design should not be "campy" or "tacky" - playful is ok, but please keep it elegant
- Website design should not be overly masculine or feminine - we will have both women and men as customers

```html
<!DOCTYPE html>
<html lang="en">
<head>
<meta charset="utf-8">
<title>Tallowmere Object Works, LLC</title>
<link href="https://fonts.googleapis.com/css2?family=Source+Sans+3:wght@200;300;400;600;700&display=swap" rel="stylesheet">
<style>
  :root {
    --ink: #1a1a1a;
    --nav-dark: #1c1c1c;
    --nav-mid: #2e2e2e;
    --brand-blue: #2a7ab8;
    --brand-blue-light: #4a9fd6;
    --sky-top: #b9dcf1;
    --tab-blue-top: #1f6fa6;
    --tab-blue-bottom: #0d4f80;
    --tab-active: #a9d6f2;
    --accent-orange: #f7931e;
    --panel-blue: #1d5f93;
    --field-blue: #c9dff0;
    --card-border: #d5d5d5;
    --muted: #6a6a6a;
    --white: #ffffff;
    --dot: #4a4a4a;
  }
  * { margin: 0; padding: 0; box-sizing: border-box; }
  html, body {
    width: 1200px; height: 1000px; overflow: hidden;
    background: var(--white);
    font-family: "Source Sans 3", sans-serif;
    color: var(--ink);
  }
  .page { position: relative; width: 1200px; height: 1000px; }

  /* top bar */
  .topbar {
    position: absolute; left: 0; top: 0; width: 1200px; height: 42px;
    background: linear-gradient(var(--nav-mid), var(--nav-dark));
    color: var(--white); font-size: 14px;
  }
  .topnav a { position: absolute; top: 13px; color: var(--white); text-decoration: none; font-weight: 600; letter-spacing: .2px; }
  .topnav a.is-active { color: var(--accent-orange); }
  .topnav a.is-active::after {
    content: ""; position: absolute; left: 50%; top: 22px; margin-left: -6px;
    border: 6px solid transparent; border-bottom-color: var(--accent-orange); border-top: 0;
  }
  .search-icon { position: absolute; left: 526px; top: 12px; }
  .search-field {
    position: absolute; left: 553px; top: 8px; width: 279px; height: 26px;
    background: var(--white); border-radius: 3px; color: #888; font-size: 11px;
    padding: 6px 10px;
  }
  .account { position: absolute; left: 873px; top: 12px; font-size: 14px; }
  .account em { font-style: italic; }
  .account strong { font-weight: 600; }
  .account .sep { margin: 0 8px; }

  /* hero */
  .hero {
    position: absolute; left: 0; top: 42px; width: 1200px; height: 560px;
    background: linear-gradient(var(--sky-top) 0%, #e6f3fb 22%, var(--white) 42%);
  }
  .brand { position: absolute; left: 144px; top: 27px; display: flex; align-items: center; }
  .brand-mark { width: 84px; height: 100px; background: var(--brand-blue); border-radius: 6px; }
  .brand-text { margin-left: 18px; }
  .brand-name { font-size: 37px; font-weight: 400; color: var(--brand-blue); line-height: 1; }
  .brand-tagline { font-size: 23px; font-weight: 400; color: var(--brand-blue-light); margin-top: 6px; }

  .login-panel {
    position: absolute; left: 945px; top: 3px; width: 191px; height: 122px;
    background: var(--panel-blue); border-radius: 4px; padding: 10px;
    box-shadow: 0 2px 5px rgba(0,0,0,.3);
  }
  .login-field {
    height: 30px; background: var(--field-blue); border-radius: 3px;
    font-size: 11px; color: #4b6a82; padding: 8px 10px; margin-bottom: 10px;
  }
  .login-button {
    position: absolute; right: 10px; bottom: 8px; width: 84px; height: 28px;
    background: #1b1b1b; color: var(--white); border-radius: 3px; font-size: 13px;
    display: flex; align-items: center; justify-content: center; gap: 8px;
  }

  .hero-photo {
    position: absolute; left: 288px; top: 165px; width: 300px; height: 265px;
    background: radial-gradient(ellipse at 50% 50%, #f2f2ef 0%, #dcdcd6 55%, rgba(255,255,255,0) 72%);
  }
  .slide-arrow {
    position: absolute; top: 270px; width: 54px; height: 54px; border-radius: 5px;
    display: flex; align-items: center; justify-content: center;
  }
  .slide-arrow.prev { left: 142px; background: #a5a5a5; }
  .slide-arrow.next { left: 995px; background: #3b3b3b; }

  .slide-copy { position: absolute; left: 628px; top: 225px; }
  .slide-title { font-size: 82px; font-weight: 200; line-height: 1; letter-spacing: -1px; }
  .slide-question { font-size: 28px; font-weight: 300; margin-top: 14px; }
  .slide-question .hl { color: var(--accent-orange); }
  .slide-note { font-size: 17px; font-weight: 400; margin-top: 2px; }

  .slide-dots { position: absolute; left: 939px; top: 435px; display: flex; gap: 13px; }
  .slide-dots span { width: 18px; height: 18px; border-radius: 50%; background: var(--dot); }
  .slide-dots span.is-current { background: var(--brand-blue); }

  /* section bar */
  .section-bar {
    position: absolute; left: 122px; top: 532px; width: 954px; height: 70px;
    background: linear-gradient(var(--tab-blue-top), var(--tab-blue-bottom));
    color: var(--white);
  }
  .section-bar::after {
    content: ""; position: absolute; left: -60px; right: -60px; top: 70px; height: 20px;
    background: radial-gradient(ellipse at 50% 0%, rgba(0,50,90,.25), rgba(255,255,255,0) 70%);
  }
  .home-tab {
    position: absolute; left: 0; top: 0; width: 76px; height: 70px;
    background: var(--accent-orange); display: flex; align-items: center; justify-content: center;
  }
  .home-tab::after {
    content: ""; position: absolute; right: -14px; top: 0;
    border-top: 35px solid transparent; border-bottom: 35px solid transparent;
    border-left: 14px solid var(--accent-orange);
  }
  .section-tab { position: absolute; top: 20px; }
  .section-tab b { display: block; font-size: 15px; font-weight: 600; }
  .section-tab small { display: block; font-size: 11px; color: #9cc3e0; }
  .section-tab.is-active {
    top: -15px; height: 85px; width: 117px; padding: 35px 0 0 0; text-align: center;
    background: var(--tab-active); border-top: 4px solid var(--accent-orange); color: #10324e;
  }
  .section-tab.is-active small { color: #4d7896; }
  .cart {
    position: absolute; left: 663px; top: 0; height: 70px; padding-left: 16px;
    border-left: 1px solid #3a7fb3; display: flex; align-items: center; gap: 10px;
  }
  .cart-label { font-size: 13px; line-height: 1.15; }
  .cart-label .count { color: var(--accent-orange); }
  .shop-button {
    position: absolute; left: 800px; top: 15px; width: 142px; height: 39px;
    background: var(--accent-orange); border-radius: 3px; color: #1a1a1a;
    font-size: 17px; font-weight: 600; display: flex; align-items: center; justify-content: center;
  }

  /* products */
  .products { position: absolute; left: 122px; top: 642px; display: flex; gap: 11px; }
  .product { width: 231px; }
  .product-frame {
    height: 142px; border: 1px solid var(--card-border); border-radius: 4px;
    box-shadow: 0 2px 4px rgba(0,0,0,.12); padding: 8px;
  }
  .product-photo { width: 100%; height: 100%; border-radius: 2px; }
  .product-photo.ring { background: radial-gradient(ellipse, #8c8c8c 0%, #d4d4d4 45%, #fafafa 72%); }
  .product-photo.fitting { background: radial-gradient(ellipse, #e9e9e3 0%, #d9d9d2 40%, #fafafa 72%); }
  .product-photo.parts { background: linear-gradient(120deg, #2a2a2a 0%, #e06a2a 40%, #3a8fd0 70%, #f2f2f2 100%); }
  .product-photo.lattice { background: linear-gradient(135deg, #c9ab8a, #e8d6c2 50%, #b8977a); }
  .product-name { font-size: 17px; font-weight: 600; margin-top: 16px; }
  .product-desc { font-size: 12px; color: var(--muted); margin-top: 2px; }
</style>
</head>
<body>
<div class="page">

  <header class="topbar">
    <nav class="topnav">
      <a href="#" style="left:163px">WHY T7</a>
      <a href="#" class="is-active" style="left:235px">DREAMER</a>
      <a href="#" style="left:320px">MAKER</a>
      <a href="#" style="left:388px">PRODUCER</a>
    </nav>
    <svg class="search-icon" width="20" height="20" viewBox="0 0 20 20">
      <circle cx="11.5" cy="8" r="5.5" fill="none" stroke="#f7931e" stroke-width="2.5"/>
      <line x1="7.5" y1="12" x2="2" y2="17.5" stroke="#f7931e" stroke-width="3" stroke-linecap="round"/>
    </svg>
    <div class="search-field">Type search here...</div>
    <div class="account"><em>Hello Guest,</em> <strong>Login</strong><span class="sep">|</span>Register</div>
  </header>

  <section class="hero">
    <div class="brand">
      <div class="brand-mark"></div>
      <div class="brand-text">
        <div class="brand-name">Tallowmere Object Works, LLC</div>
        <div class="brand-tagline">Making Your Ideas Into Objects</div>
      </div>
    </div>

    <form class="login-panel">
      <div class="login-field">Username</div>
      <div class="login-field">Password</div>
      <div class="login-button">Login
        <svg width="16" height="16" viewBox="0 0 16 16"><circle cx="8" cy="8" r="8" fill="#f7931e"/><path d="M6 4.5 L11 8 L6 11.5Z" fill="#1b1b1b"/></svg>
      </div>
    </form>

    <div class="slide-arrow prev">
      <svg width="22" height="26" viewBox="0 0 22 26"><path d="M20 1 L2 13 L20 25Z" fill="#fff"/></svg>
    </div>
    <div class="hero-photo" role="img" aria-label="White 3D-printed pipe fitting with threaded ends and a perforated inner cage"></div>
    <div class="slide-copy">
      <div class="slide-title">BUY</div>
      <div class="slide-question">Find <span class="hl">ONE</span> you like?</div>
      <div class="slide-note">We can make and deliver it!</div>
    </div>
    <div class="slide-arrow next">
      <svg width="22" height="26" viewBox="0 0 22 26"><path d="M2 1 L20 13 L2 25Z" fill="#fff"/></svg>
    </div>
    <div class="slide-dots"><span class="is-current"></span><span></span><span></span><span></span></div>
  </section>

  <nav class="section-bar">
    <div class="home-tab">
      <svg width="36" height="32" viewBox="0 0 36 32"><path d="M18 2 L2 16 H7 V30 H15 V21 H21 V30 H29 V16 H34Z" fill="#fff"/></svg>
    </div>
    <div class="section-tab" style="left:92px"><b>ABOUT T7</b><small>Nam liber tempor</small></div>
    <div class="section-tab is-active" style="left:193px"><b>DREAM</b><small>Nobis eleifend</small></div>
    <div class="section-tab" style="left:342px"><b>MAKE</b><small>Dolor sit amet</small></div>
    <div class="section-tab" style="left:450px"><b>PRODUCE</b><small>Adipiscing conse</small></div>
    <div class="section-tab" style="left:582px"><b>SELL</b><small>Ed delivero</small></div>
    <div class="cart">
      <svg width="34" height="30" viewBox="0 0 34 30">
        <path d="M1 3 H7 L11 20 H28 L32 8 H9" fill="none" stroke="#fff" stroke-width="2.2" stroke-linejoin="round"/>
        <path d="M12 11 H30 M13 15 H29" stroke="#fff" stroke-width="1.5"/>
        <circle cx="13" cy="25" r="2.8" fill="#fff"/><circle cx="26" cy="25" r="2.8" fill="#fff"/>
      </svg>
      <div class="cart-label">Shopping<br>Chart <span class="count">(0)</span></div>
    </div>
    <div class="shop-button">Shopping NOW!</div>
  </nav>

  <section class="products">
    <article class="product">
      <div class="product-frame"><div class="product-photo ring" role="img" aria-label="Grey 3D-printed interlocking ring sculpture"></div></div>
      <div class="product-name">Product 1</div>
      <div class="product-desc">Nam liber tempor cum soluta</div>
    </article>
    <article class="product">
      <div class="product-frame"><div class="product-photo fitting" role="img" aria-label="White 3D-printed pipe fitting"></div></div>
      <div class="product-name">Product 1</div>
      <div class="product-desc">Nam liber tempor cum soluta</div>
    </article>
    <article class="product">
      <div class="product-frame"><div class="product-photo parts" role="img" aria-label="Assortment of colourful plastic printed parts"></div></div>
      <div class="product-name">Product 1</div>
      <div class="product-desc">Nam liber tempor cum soluta</div>
    </article>
    <article class="product">
      <div class="product-frame"><div class="product-photo lattice" role="img" aria-label="Beige printed lattice structure with leaf-shaped openings"></div></div>
      <div class="product-name">Product 1</div>
      <div class="product-desc">Nam liber tempor cum soluta</div>
    </article>
  </section>

</div>
</body>
</html>
```